Business Card Design

We would like to re-design our business cards. Our Company - Qwinrel Turbochargers, rebuilds turbochargers and sells replacement parts. Our website is: http://www.qwinrelturbochargers-example.com
We just had our logo changed. I will attach the file. Looking for fresh new/modern business card. We like the colors red, black, white and silver. Black background looks attractive, but not a requirement. The final design should communicate reasonable/competitive prices, top quality and reliability of our products.
Updates
Project Deadline Extended
Reason: Need to finalize the info on the card. Currently working on changing address and email info. Want to make sure it is the correct one before accepting the final design. Unless, this is something that can be changed at a later time..??
Industry/Entity Type
Business
Contact Information for Business Card
QWINREL TURBOCHARGERS, LLC
20473 Harwick Lane NE
Massillon, OH 44647
Tel: +1-555-214-7390
Fax: +1-555-267-1842
info@QwinrelTurbochargers-example.com
Our current business card had the following highlights:
*We rebuild all Turbocharges for Automotive, Diesel and Industrial
*Precision Balancing and in-house turbocharger needs
*All Turbocharger replacement parts are made in USA / U.K.
Look and feel
Each slider illustrates characteristics of the customer's brand and the style your logo design should communicate.

```html
<!DOCTYPE html>
<html lang="en">
<head>
<meta charset="utf-8">
<title>Qwinrel Turbochargers – Business Card</title>
<link rel="stylesheet" href="https://fonts.googleapis.com/css2?family=Open+Sans:wght@400;600;700&display=swap">
<style>
  :root {
    --red: #e31e24;
    --red-dark: #b5121b;
    --black: #0d0a0b;
    --white: #ffffff;
    --silver: #c9c3c4;
    --ink: #1a1a1a;
    --bg-top: #f4f4f4;
    --bg-bottom: #cfcfcf;
  }
  * { box-sizing: border-box; margin: 0; padding: 0; }
  html, body { width: 1200px; height: 873px; overflow: hidden; }
  body {
    font-family: "Open Sans", Arial, sans-serif;
    background: linear-gradient(180deg, var(--bg-top), var(--bg-bottom));
    position: relative;
  }
  .card {
    position: absolute;
    top: 282px;
    width: 540px;
    height: 308px;
    overflow: hidden;
    box-shadow: 0 6px 18px rgba(0,0,0,.28);
    background: var(--white);
  }
  .card--front { left: 40px; }
  .card--back { left: 620px; }
  .card__art { position: absolute; inset: 0; width: 540px; height: 308px; }

  .brand {
    position: absolute;
    display: flex;
    align-items: center;
    gap: 10px;
    color: var(--ink);
    font-weight: 700;
    font-size: 30px;
    letter-spacing: -.3px;
    white-space: nowrap;
  }
  .brand__dot {
    width: 22px; height: 22px; border-radius: 50%;
    background: var(--red);
    flex: none;
  }
  .card--front .brand { left: 0; right: 0; justify-content: center; top: 46px; }
  .card--back .brand { left: 0; right: 0; justify-content: center; top: 236px; }

  .web {
    position: absolute;
    left: 0; right: 0; top: 232px;
    text-align: center;
    color: var(--white);
    font-size: 15px;
  }
  .web__accent { color: var(--red); }

  .person {
    position: absolute; left: 24px; top: 22px; color: var(--white);
  }
  .person__name { font-size: 21px; font-weight: 400; line-height: 1.1; }
  .person__role { font-size: 11px; margin-top: 4px; color: var(--black); }
  .address {
    position: absolute; left: 24px; top: 95px;
    color: var(--white); font-size: 15px; line-height: 1.35;
  }
  .contacts {
    position: absolute; right: 20px; top: 60px;
    list-style: none; color: var(--white);
    font-size: 13px; line-height: 1.35; text-align: right;
  }
  .contacts li { display: flex; justify-content: flex-end; align-items: center; gap: 6px; }
  .contacts svg { width: 13px; height: 13px; flex: none; }
</style>
</head>
<body>

<section class="card card--front" aria-label="Business card front">
  <svg class="card__art" viewBox="0 0 540 308" aria-hidden="true">
    <path d="M0,150 C170,112 350,118 540,176" fill="none" stroke="var(--silver)" stroke-width="6"/>
    <path d="M0,156 C170,118 350,124 540,182 L540,308 L0,308 Z" fill="var(--black)"/>
    <path d="M0,158 C170,120 350,126 540,184" fill="none" stroke="var(--red)" stroke-width="5"/>
  </svg>
  <div class="brand"><span class="brand__dot"></span>Qwinrel Turbochargers</div>
  <p class="web">www.<span class="web__accent">qwinrelturbochargers-example</span>.com</p>
</section>

<section class="card card--back" aria-label="Business card back">
  <svg class="card__art" viewBox="0 0 540 308" aria-hidden="true">
    <path d="M0,0 L540,0 L540,196 C360,160 180,150 0,164 Z" fill="var(--red)"/>
    <path d="M0,168 C180,154 360,164 540,200" fill="none" stroke="var(--black)" stroke-width="3"/>
    <path d="M0,176 C180,162 360,172 540,208" fill="none" stroke="var(--silver)" stroke-width="8"/>
  </svg>
  <div class="person">
    <p class="person__name">Marcus Delwin</p>
    <p class="person__role">Director</p>
  </div>
  <p class="address">4817 Brandell Ave. NW<br>North&nbsp; Carvey.Ohio</p>
  <ul class="contacts">
    <li>+1-555-214-7390
      <svg viewBox="0 0 16 16"><path d="M3 1l3 3-1.5 2a9 9 0 005.5 5.5L12 10l3 3-2 2C7 15 1 9 1 3z" fill="var(--black)"/></svg></li>
    <li>+1-555-267-1842
      <svg viewBox="0 0 16 16"><rect x="4" y="1" width="8" height="5" fill="var(--black)"/><rect x="1" y="6" width="14" height="7" rx="1" fill="var(--black)"/><rect x="4" y="11" width="8" height="4" fill="var(--white)" stroke="var(--black)"/></svg></li>
    <li>info@QwinrelTurbochargers-example.com
      <svg viewBox="0 0 16 16"><rect x="1" y="3" width="14" height="10" fill="var(--black)"/><path d="M1 3l7 6 7-6" fill="none" stroke="var(--white)" stroke-width="1.2"/></svg></li>
    <li>www.qwinrelturbochargers-example.com
      <svg viewBox="0 0 16 16"><circle cx="8" cy="8" r="7" fill="var(--black)"/><path d="M1 8h14M8 1v14M3 4h10M3 12h10" stroke="var(--red)" stroke-width="1" fill="none"/><ellipse cx="8" cy="8" rx="3" ry="7" fill="none" stroke="var(--red)"/></svg></li>
  </ul>
  <div class="brand"><span class="brand__dot"></span>Qwinrel Turbochargers</div>
</section>

</body>
</html>
```